Hollow Thicket, a 3d voxel survival video game needs a card for gaming conventions

I am the lead developer for Hollow Thicket http://www.HollowThicket.example and need a business card to hand out at an indie gaming convention
The card would need to include the game name, website url, my name, position (Lead Developer), e-mail and phone number
The game is a 3d, voxel (with smooth terrain) based survival game with guns and wildlife. The main icon of the game would likely be a grizzly bear but I am willing to accept other designs too.
Attached is a media kit for the game with some images you can use but don't have to its just what little art I can provide. Anything on the website or from the video game can also be used. unrelated art can also be used.
Target Market(s)
Indie Developers/publishers at conferences
Industry/Entity Type
Games
Contact Information for Business Card
Name: Corin Waldrick
Position: Lead Developer
E-mail: Pale_Kettle@mailbox.example
Phone number: 555-372-1186

```html
<!DOCTYPE html>
<html lang="en">
<head>
<meta charset="utf-8">
<title>Hollow Thicket — Business Card</title>
<link href="https://fonts.googleapis.com/css2?family=Open+Sans:wght@400;600;700;800&display=swap" rel="stylesheet">
<style>
  :root {
    --backdrop: #3b3532;
    --card: #0d0c0c;
    --card-edge: #1a1818;
    --brand-red: #b53a27;
    --accent-orange: #d9772b;
    --text-light: #ece6df;
    --fur-dark: #3a2a1d;
    --fur-mid: #6b5038;
    --fur-light: #9a7b5a;
  }
  * { box-sizing: border-box; margin: 0; padding: 0; }
  html, body { width: 1200px; height: 900px; overflow: hidden; }
  body {
    background: var(--backdrop);
    font-family: "Open Sans", Arial, sans-serif;
    position: relative;
  }
  .card {
    position: absolute;
    top: 300px;
    width: 520px;
    height: 300px;
    background: var(--card);
    border: 1px solid var(--card-edge);
    box-shadow: 0 14px 30px rgba(0,0,0,0.45);
    overflow: hidden;
  }
  .card--front { left: 50px; }
  .card--back { left: 630px; }

  .wildlife-photo {
    position: absolute;
    left: 20px;
    bottom: 0;
    width: 220px;
    height: 215px;
    border-radius: 48% 52% 0 0 / 42% 40% 0 0;
    background: radial-gradient(ellipse at 55% 35%, var(--fur-light) 0%, var(--fur-mid) 45%, var(--fur-dark) 100%);
  }

  .brand-name {
    font-weight: 800;
    color: var(--brand-red);
    text-transform: uppercase;
    letter-spacing: 2px;
    line-height: 1.05;
  }
  .card--front .brand-name {
    position: absolute;
    left: 270px;
    top: 48px;
    font-size: 26px;
  }
  .contact-block {
    position: absolute;
    left: 262px;
    top: 138px;
    color: var(--text-light);
  }
  .person-name {
    font-size: 17px;
    font-weight: 700;
    color: var(--accent-orange);
  }
  .person-role {
    font-size: 12.5px;
    margin-top: 2px;
  }
  .contact-list {
    list-style: none;
    margin-top: 14px;
    font-size: 12.5px;
  }
  .contact-list li {
    display: flex;
    align-items: center;
    gap: 7px;
    margin-bottom: 4px;
  }
  .contact-icon { width: 11px; height: 11px; flex: none; }

  .card--back {
    display: flex;
    flex-direction: column;
    align-items: center;
    justify-content: center;
  }
  .card--back .brand-name {
    font-size: 40px;
    text-align: center;
  }
  .back-url {
    margin-top: 22px;
    font-size: 14px;
    font-weight: 600;
    color: var(--accent-orange);
  }
</style>
</head>
<body>
  <section class="card card--front">
    <div class="wildlife-photo" role="img" aria-label="Photo of a roaring grizzly bear"></div>
    <div class="brand-name">Hollow<br>Thicket</div>
    <div class="contact-block">
      <div class="person-name">Corin Waldrick</div>
      <div class="person-role">Lead Developer</div>
      <ul class="contact-list">
        <li>
          <svg class="contact-icon" viewBox="0 0 12 12" aria-hidden="true">
            <path d="M3 1 L5 3 L4 4.5 Q5 7 7.5 8 L9 7 L11 9 L9.5 11 Q4 10.5 1 3 Z" fill="var(--accent-orange)"/>
          </svg>
          555-372-1186
        </li>
        <li>
          <svg class="contact-icon" viewBox="0 0 12 12" aria-hidden="true">
            <rect x="0.5" y="2" width="11" height="8" fill="var(--accent-orange)"/>
            <path d="M0.5 2 L6 7 L11.5 2" fill="none" stroke="#0d0c0c" stroke-width="1"/>
          </svg>
          Pale_Kettle@mailbox.example
        </li>
        <li>
          <svg class="contact-icon" viewBox="0 0 12 12" aria-hidden="true">
            <circle cx="6" cy="6" r="5.5" fill="var(--accent-orange)"/>
            <ellipse cx="6" cy="6" rx="2.3" ry="5" fill="none" stroke="#0d0c0c" stroke-width="0.8"/>
            <line x1="1" y1="6" x2="11" y2="6" stroke="#0d0c0c" stroke-width="0.8"/>
          </svg>
          www.HollowThicket.example
        </li>
      </ul>
    </div>
  </section>

  <section class="card card--back">
    <div class="brand-name">Hollow<br>Thicket</div>
    <div class="back-url">www.HollowThicket.example</div>
  </section>
</body>
</html>
```